BUSINESS CARD DESIGN

NAME- DALE VORSKIN
PHONE NUMER - 555- 714-9082
EMAIL- OFFICE@TRV-GROUNDMAKRZ.COM
BACK OF CARD- SPEACIALIZES IN LAND CLEARING, FORESTRY MUCLHING AND EXCAVATION

Contact Information for Business Card

NAME- DALE VORSKIN PHONE NUMER - 555- 714-9082 EMAIL- OFFICE@TRV-GROUNDMAKRZ.COM BACK OF CARD- SPEACIALIZES IN LAND CLEARING , MUCLHING AND EXCAVATION

```html
<!DOCTYPE html>
<html lang="en">
<head>
<meta charset="utf-8">
<title>Terravale Groundmakrz – Business Card</title>
<link href="https://fonts.googleapis.com/css2?family=Montserrat:wght@400;500;600;700&display=swap" rel="stylesheet">
<style>
  :root {
    --backdrop: #6b6b6b;
    --card: #1b1b1b;
    --card-edge: #0f0f0f;
    --silver: #d9d9d9;
    --gold: #f5b21b;
    --white: #f2f2f2;
  }
  * { margin: 0; padding: 0; box-sizing: border-box; }
  html, body { width: 1200px; height: 1000px; overflow: hidden; }
  body {
    background: var(--backdrop);
    font-family: "Montserrat", sans-serif;
    position: relative;
  }
  .card {
    position: absolute;
    left: 198px;
    width: 804px;
    height: 460px;
    border-radius: 18px;
    background: linear-gradient(160deg, #262626 0%, var(--card) 55%, var(--card-edge) 100%);
    overflow: hidden;
  }
  .card--front { top: 32px; }
  .card--back { top: 508px; background: linear-gradient(120deg, #222 0%, var(--card) 60%, #050505 100%); }

  /* front */
  .brand-front {
    position: absolute; left: 0; right: 0; top: 40px;
    display: flex; flex-direction: column; align-items: center;
    color: var(--silver);
  }
  .brand-front .brand-mark {
    width: 150px; height: 150px; border-radius: 50%;
    border: 6px solid var(--silver);
  }
  .brand-front .brand-name {
    margin-top: 40px; font-weight: 600; font-size: 34px; letter-spacing: 2px;
  }
  .brand-front .brand-phone {
    margin-top: 18px; font-weight: 500; font-size: 20px; letter-spacing: 12px;
    padding-top: 10px; border-top: 2px solid var(--silver);
  }
  .front-rule {
    position: absolute; left: 0; right: 0; top: 390px; height: 3px;
    background: linear-gradient(90deg, #9a9a9a, #e6e6e6, #9a9a9a);
  }
  .service {
    position: absolute; top: 412px;
    color: var(--white); font-weight: 500; font-size: 16.5px;
    display: flex; align-items: center; gap: 6px;
  }
  .service::before {
    content: ""; width: 8px; height: 12px;
    border-left: 3px solid var(--gold); border-right: 3px solid var(--gold);
  }
  .service--clearing { left: 120px; }
  .service--excavation { left: 450px; }

  /* back */
  .brand-back {
    position: absolute; left: 30px; width: 254px; top: 160px;
    display: flex; flex-direction: column; align-items: center;
    color: var(--gold);
  }
  .brand-back .brand-mark {
    width: 110px; height: 110px; border-radius: 50%;
    border: 5px solid var(--gold);
  }
  .brand-back .brand-name {
    margin-top: 18px; font-weight: 700; font-size: 17px; text-align: center; line-height: 1.3;
  }
  .brand-back .brand-phone {
    margin-top: 6px; font-weight: 600; font-size: 12px; letter-spacing: 7px;
  }
  .holder {
    position: absolute; left: 0; top: 374px;
    display: flex; align-items: center; gap: 12px;
  }
  .holder::before { content: ""; width: 22px; height: 24px; background: var(--gold); }
  .holder-name { color: var(--gold); font-weight: 600; font-size: 30px; letter-spacing: 0.5px; }
  .contact {
    position: absolute; left: 320px;
    display: flex; align-items: center; gap: 12px;
    color: var(--white); font-weight: 400;
  }
  .contact svg { width: 28px; height: 28px; }
  .contact--phone { top: 350px; font-size: 24px; }
  .contact--email { top: 391px; font-size: 21px; }
</style>
</head>
<body>

<section class="card card--front">
  <div class="brand-front">
    <div class="brand-mark"></div>
    <div class="brand-name">TERRAVALE GROUNDMAKRZ LLC</div>
    <div class="brand-phone">555-714-9082</div>
  </div>
  <div class="front-rule"></div>
  <p class="service service--clearing">Speacializes In Land Clearing</p>
  <p class="service service--excavation">Mulching And Excavation</p>
</section>

<section class="card card--back">
  <div class="brand-back">
    <div class="brand-mark"></div>
    <div class="brand-name">TERRAVALE GROUNDMAKRZ LLC</div>
    <div class="brand-phone">555-714-9082</div>
  </div>

  <div class="holder"><span class="holder-name">DALE VORSKIN</span></div>

  <div class="contact contact--phone">
    <svg viewBox="0 0 28 28" fill="none" stroke="var(--gold)" stroke-width="2" stroke-linejoin="round">
      <path d="M6 4 L10 4 L12 10 L9 12 Q12 18 16 20 L18 17 L24 19 L24 23 Q24 25 21 25 Q4 22 3 7 Q3 4 6 4 Z"/>
      <path d="M16 3 H26 V11 H20 L17 14 V11 H16 Z"/>
    </svg>
    <span>555- 714-9082</span>
  </div>

  <div class="contact contact--email">
    <svg viewBox="0 0 28 28" fill="none" stroke="var(--gold)" stroke-width="2" stroke-linejoin="round">
      <path d="M3 13 L25 4 L18 25 L13 16 Z"/>
      <path d="M13 16 L25 4"/>
    </svg>
    <span>OFFICE@TRV-GROUNDMAKRZ.COM</span>
  </div>
</section>

</body>
</html>
```